Smack you in the face - Landing page for Residential Electrical Repairs (Searchly Ads)

I need an effective landing page for Searchly ads. The ads will target residential electrical repairs. Lighting Outages, Power Outages, Breakers Tripping, Outlets Not Working. I need a strong call to action to Call Us Now! Forms don't work well for us so we only need one form as a last option at the bottom of the page. We only work on homes. the website is https://www.vantor-wiring.example/
email is : support@vantor-wiring.example
Phone 555-217-4086

**This is about one focused service. Electrical Repairs - That includes Partial Power Outages, Outlets Not Working, Tripped Breakers, Electrical Panel repairs, and Fusebox Repairs. The area served will only be Greenville, SC. KOBA is the platform

Target Market(s)

Homeonwers in need of electrical repair

Industry/Entity Type

Residential Electricians

Coding

Coded - Design and coding required

Requirements
Must have
• Strong to action for phone calls, this landing page must grab action fast.
Nice to have
• Social proof with existing 5 start reviews for Searchly, Rately, TCB, and Friendnet
Should not have
• Should not be form based. I do not like the site's current them, please don't copy it. Make your own.

```html
<!DOCTYPE html>
<html lang="en">
<head>
<meta charset="utf-8">
<title>Vantor Wiring – Residential Electrical Repairs</title>
<link rel="stylesheet" href="https://fonts.googleapis.com/css2?family=Montserrat:wght@600;700&family=Roboto:wght@400;500;700&display=swap">
<style>
:root{
  --blue:#1e8fc3;
  --blue-dark:#1a7fb0;
  --blue-light:#3aa3d3;
  --orange:#f26a22;
  --white:#ffffff;
  --ink:#111111;
  --text:#555555;
  --card:#f3f3f3;
}
*{box-sizing:border-box;margin:0;padding:0}
html,body{width:1200px;height:3429px;overflow:hidden}
body{font-family:"Roboto",Arial,sans-serif;color:var(--text);background:var(--white);position:relative}
a{text-decoration:none}
h1,h2,h3{font-family:"Montserrat",Arial,sans-serif;font-weight:700}

/* hero */
.hero{position:absolute;left:0;top:0;width:1200px;height:746px;background:var(--blue);overflow:hidden}
.hero-deco{position:absolute;left:-130px;top:-250px;width:450px;height:490px;border-radius:50%;background:var(--blue-light);opacity:.55}
.hero-card{position:absolute;left:110px;top:146px;width:978px;height:374px;background:var(--blue-dark);border-radius:6px}
.hero-right{position:absolute;left:1088px;top:220px;width:112px;height:300px;background:var(--blue-light);opacity:.4;border-radius:60px 0 0 60px}
.logo{position:absolute;left:110px;top:30px;color:var(--white);font-family:"Montserrat",sans-serif;font-weight:700;display:flex;align-items:center;gap:10px;font-size:22px;letter-spacing:1px}
.logo .dot{width:34px;height:34px;border-radius:50%;border:3px solid var(--white)}
.nav{position:absolute;left:416px;top:52px;display:flex;font-size:14px}
.nav a{color:var(--white);margin-right:29px;padding-bottom:9px;position:relative}
.nav a.active::after{content:"";position:absolute;left:0;right:0;bottom:0;height:3px;background:var(--white)}
.search{position:absolute;left:1073px;top:53px}
.hero h1{position:absolute;left:175px;top:222px;color:var(--white);font-size:44px;line-height:52px;width:360px}
.btn{display:inline-block;background:var(--orange);color:var(--white);font-family:"Roboto",sans-serif;font-weight:700;font-size:13px;text-transform:uppercase;border-radius:22px;text-align:center;line-height:42px;box-shadow:0 3px 6px rgba(0,0,0,.15);text-decoration:none}
.hero .btn{position:absolute;left:174px;top:444px;width:171px}
.dots{position:absolute;left:173px;top:606px;display:flex;gap:7px}
.dots span{width:10px;height:10px;border-radius:50%;background:#d7e9f3}
.dots span.on{background:var(--orange);box-shadow:0 0 0 2px var(--white)}
.hero-photo{position:absolute;left:555px;top:100px}

/* about */
.about-photo{position:absolute;left:110px;top:848px;width:473px;height:428px;border-radius:18px;background:linear-gradient(160deg,#2b4a86,#1b2c5a 55%,#6d7c95);overflow:hidden}
.call-box{position:absolute;left:0;top:266px;width:240px;height:134px;background:var(--white);border-radius:0 16px 16px 0;padding:40px 0 0 7px}
.call-box .lbl{font-size:14px;font-weight:700;color:var(--ink);display:flex;align-items:center;gap:10px}
.call-box .num{font-family:"Montserrat",sans-serif;font-weight:700;font-size:27px;color:var(--ink);margin-top:6px;white-space:nowrap}
.about h2{position:absolute;left:625px;top:840px;font-size:44px;color:var(--ink)}
.about p{position:absolute;left:625px;top:908px;width:463px;font-size:13.5px;line-height:25.7px;text-align:justify}
.about .btn{position:absolute;left:625px;top:1234px;width:171px}

/* repairs */
.repairs{position:absolute;left:0;top:1380px;width:1200px;height:607px;background:var(--orange)}
.repairs h2{position:absolute;left:0;width:1200px;top:92px;text-align:center;color:var(--white);font-size:44px}
.service{position:absolute;top:190px;width:232px;text-align:center}
.service .pic{width:232px;height:232px;border-radius:50%;border:5px solid var(--white)}
.service h3{font-family:"Roboto",sans-serif;color:var(--white);font-size:21px;line-height:26px;margin-top:14px;font-weight:700}
.arrow{position:absolute}

/* testimonials */
.testi h2{position:absolute;left:0;width:1200px;top:2080px;text-align:center;font-size:44px;color:var(--ink)}
.platforms{position:absolute;left:0;width:1200px;top:2150px;display:flex;justify-content:center;gap:12px;font-size:12px;font-weight:700;color:var(--blue)}
.total{position:absolute;left:0;width:1200px;top:2192px;text-align:center;font-size:14px}
.card{position:absolute;top:2236px;width:297px;height:319px;background:var(--card);border-radius:4px;text-align:center;padding:36px 26px 0}
.stars{color:var(--orange);font-size:16px;letter-spacing:6px}
.card p{font-size:13.5px;line-height:21.5px;margin-top:18px;height:108px}
.card .who{font-size:13.5px;font-weight:700;color:var(--ink);margin-top:12px}
.card .src{margin:34px auto 0;display:inline-flex;align-items:center;gap:6px;font-weight:700;font-size:14px;color:var(--blue)}
.card .src i{width:12px;height:12px;border-radius:50%;background:var(--blue)}

/* contact */
.contact{position:absolute;left:0;top:2662px;width:1200px;height:676px;background:linear-gradient(180deg,#2a93c6,#1c86ba)}
.contact h2{position:absolute;left:0;width:1200px;top:82px;text-align:center;color:var(--white);font-size:43px;line-height:54px}
.field{position:absolute;border:2px solid var(--white);color:var(--white);font-size:14px;padding:0 24px;line-height:64px}
.contact .btn{position:absolute;left:514px;top:516px;width:170px;line-height:40px}
.footer{position:absolute;left:0;top:3372px;width:1200px;text-align:center;font-size:13.5px;color:var(--ink)}
</style>
</head>
<body>

<section class="hero">
  <div class="hero-deco"></div>
  <div class="hero-card"></div>
  <div class="hero-right"></div>
  <div class="logo"><span class="dot"></span>VANTOR WIRING</div>
  <nav class="nav">
    <a class="active" href="#">Home</a><a href="#">Our Services</a><a href="#">About Us</a><a href="#">Employment</a><a href="#">Blog</a><a href="#">Contact</a><a href="#">Areas We Serve</a>
  </nav>
  <svg class="search" width="14" height="14" viewBox="0 0 14 14"><circle cx="6" cy="6" r="4.5" fill="none" stroke="#fff" stroke-width="2"/><line x1="9.5" y1="9.5" x2="13" y2="13" stroke="#fff" stroke-width="2"/></svg>
  <h1>Your Trusted Source for Electrical Solutions</h1>
  <a class="btn" href="tel:5552174086">Call Us Now!</a>
  <div class="dots"><span class="on"></span><span></span><span></span><span></span></div>
  <svg class="hero-photo" width="520" height="600" viewBox="0 0 520 600" role="img" aria-label="Two electricians in blue uniforms servicing an outdoor unit">
    <defs><linearGradient id="ph" x1="0" y1="0" x2="1" y2="1"><stop offset="0" stop-color="#d9dcd6"/><stop offset=".5" stop-color="#3f6fa8"/><stop offset="1" stop-color="#2d2f33"/></linearGradient></defs>
    <ellipse cx="266" cy="312" rx="170" ry="300" transform="rotate(38 266 312)" fill="var(--orange)"/>
    <ellipse cx="262" cy="302" rx="164" ry="292" transform="rotate(38 262 302)" fill="#fff"/>
    <ellipse cx="262" cy="302" rx="158" ry="286" transform="rotate(38 262 302)" fill="url(#ph)"/>
  </svg>
</section>

<section class="about">
  <div class="about-photo" role="img" aria-label="Team of electricians standing in front of a branded service truck">
    <div class="call-box">
      <div class="lbl"><svg width="14" height="14" viewBox="0 0 24 24"><path fill="#f26a22" d="M6.6 10.8a15 15 0 006.6 6.6l2.2-2.2c.3-.3.7-.4 1-.2 1.1.4 2.3.6 3.6.6.6 0 1 .4 1 1V20c0 .6-.4 1-1 1A17 17 0 013 4c0-.6.4-1 1-1h3.5c.6 0 1 .4 1 1 0 1.3.2 2.5.6 3.6.1.3 0 .7-.2 1z"/></svg>Call Us</div>
      <div class="num">(555) 217-4086</div>
    </div>
  </div>
  <h2>About Us</h2>
  <p>At Vantor Wiring, EV Chargers, &amp; Generators, your electrical emergency is our urgency. We have Licensed Electricians in Greenville, SC, Raleigh, NC, and Charlotte, NC, ensuring top-tier service for every call. We've built our reputation as the go-to Emergency Electrician for homeowners in need. When you find yourself thinking about an "electrician near me," think of us. While many electrical contractors chase after large-scale construction and commercial building projects, we prioritize you – the homeowner. We're committed to delivering unbeatable same-day service for all your residential electrical repairs, EV chargers, and Generator installations. With us, you're not just another job; you're our top priority. Choose Vantor Wiring for swift, safe, and standout electrical solutions.</p>
  <a class="btn" href="tel:5552174086">Call Us Now!</a>
</section>

<section class="repairs">
  <h2>Electrical Repairs</h2>
  <svg class="arrow" style="left:44px;top:368px" width="16" height="26" viewBox="0 0 16 26"><path d="M13 2L3 13l10 11" fill="none" stroke="#fff" stroke-width="3"/></svg>
  <svg class="arrow" style="left:1134px;top:368px" width="16" height="26" viewBox="0 0 16 26"><path d="M3 2l10 11L3 24" fill="none" stroke="#fff" stroke-width="3"/></svg>
  <div class="service" style="left:105px"><div class="pic" role="img" aria-label="Electrician in orange jacket working in winter" style="background:linear-gradient(135deg,#c9d3dc,#d86a2a 60%,#3b3b3b)"></div><h3>Partial Power<br>Outages</h3></div>
  <div class="service" style="left:357px"><div class="pic" role="img" aria-label="Two workers in hard hats inspecting wiring" style="background:linear-gradient(135deg,#6b4a22,#d99a3c 50%,#2e2a24)"></div><h3>Outlets Not<br>Working</h3></div>
  <div class="service" style="left:610px"><div class="pic" role="img" aria-label="Finger switching a breaker in a panel" style="background:linear-gradient(180deg,#e7e9ea,#f0a268 50%,#d9c1a8)"></div><h3>Tripped Breakers</h3></div>
  <div class="service" style="left:862px"><div class="pic" role="img" aria-label="Electrician repairing an electrical panel" style="background:linear-gradient(135deg,#cfd6dd,#2e5e99 55%,#1e2a3a)"></div><h3>Electrical Panel<br>repairs</h3></div>
</section>

<section class="testi">
  <h2>Testimonials</h2>
  <div class="platforms"><span>Searchly</span><span>Rately</span><span>TCB</span><span>Friendnet</span></div>
  <div class="total">270 Total Reviews</div>
  <svg class="arrow" style="left:44px;top:2381px" width="16" height="26" viewBox="0 0 16 26"><path d="M13 2L3 13l10 11" fill="none" stroke="#222" stroke-width="3"/></svg>
  <svg class="arrow" style="left:1134px;top:2381px" width="16" height="26" viewBox="0 0 16 26"><path d="M3 2l10 11L3 24" fill="none" stroke="#222" stroke-width="3"/></svg>
  <div class="card" style="left:110px"><div class="stars">★★★★★</div><p>Mark and Owen were excellent in finding the problem. I appreciate their professionalism, patience, and problem solving skills! You have earned a trusted customer!</p><div class="who">Reed Calloway</div><div class="src"><i></i>Searchly</div></div>
  <div class="card" style="left:451px"><div class="stars">★★★★★</div><p>Searched to find an electrician and TEO from Hillside electric responded. He was very friendly, professional and showed interest in my dilemma. He made it easy to talk to and help me</p><div class="who">Nora Whitfield</div><div class="src"><i></i>Searchly</div></div>
  <div class="card" style="left:791px"><div class="stars">★★★★★</div><p>Mark was wonderful and immediately identified what was tripping an electrical breaker box out by our pool. He then installed an electrical outlet for me that I requested in the attic;</p><div class="who">marisol dunne</div><div class="src"><i></i>Searchly</div></div>
</section>

<section class="contact" role="region" aria-label="Contact form">
  <h2>Your Electrical Needs,<br>Our Expertise - Contact Us!</h2>
  <div class="field" style="left:155px;top:220px;width:431px;height:68px">Name</div>
  <div class="field" style="left:155px;top:323px;width:431px;height:68px">Email</div>
  <div class="field" style="left:155px;top:426px;width:431px;height:68px">Phone</div>
  <div class="field" style="left:612px;top:220px;width:431px;height:274px">Text here...</div>
  <a class="btn" href="#">Submit Now</a>
</section>

<footer class="footer">Copyright © 2023 Companyname. All Rights Reserved.</footer>

</body>
</html>
```